Private Investment Firm Needs PowerPoint Presentation Template

Design PowerPoint template, take Pinebrook-submitted rough presentation draft, and drop it into new template. See attached Project Brief file for more detail.
Updates

Some decent designs have been submitted but they seem to lack the understanding of our target markets. I am hopeful that more time and feedback will result in better results.

Target Market(s)

Private company owners and intermediaries.

Font styles to use
Serif

Colors
3176b5

Requirements
Must have
• See attached Project Brief.
Nice to have
Should not have
• No B2C fluff--this is a B2B project.

```html
<!DOCTYPE html>
<html lang="en">
<head>
<meta charset="utf-8">
<title>Non-Control Capital Questionnaire</title>
<link href="https://fonts.googleapis.com/css2?family=Cinzel:wght@500&family=Montserrat:wght@400;600;700&display=swap" rel="stylesheet">
<style>
:root{
  --blue:#1f6fb8;
  --blue-dark:#1559a0;
  --charcoal:#38393b;
  --grey:#5c5d60;
  --text:#222;
  --muted:#555;
  --page:#e9e9ea;
}
*{margin:0;padding:0;box-sizing:border-box}
html,body{width:1200px;height:770px;overflow:hidden;background:var(--page)}
body{font-family:"Montserrat",Arial,sans-serif;color:var(--text)}
.slide{position:absolute;left:0;top:47px;width:1200px;height:675px;background:linear-gradient(180deg,#fff 0%,#f6f7f9 100%);overflow:hidden}
.kicker{position:absolute;top:28px;left:0;width:100%;text-align:center;font-weight:700;font-size:25px;color:var(--blue)}
.rule{position:absolute;top:44px;height:2px;background:#8c8d90}
.rule-left{left:0;width:349px}
.rule-right{left:859px;right:0}
.banner{position:absolute;top:83px;left:0;width:1200px;height:98px}
.banner-title{position:absolute;top:83px;left:0;width:1200px;height:98px;display:flex;flex-direction:column;justify-content:center;align-items:center;font-family:"Cinzel",Georgia,serif;font-weight:500;color:#fff;font-size:28px;line-height:35px;letter-spacing:.5px}
.tab{position:absolute;top:196px;left:474px;width:220px;height:34px}
.tab-label{position:absolute;top:196px;left:474px;width:220px;height:34px;line-height:34px;text-align:center;color:#fff;font-weight:700;font-size:23px}
.item{position:absolute;width:530px;font-size:11.6px;line-height:13.6px;color:var(--muted);letter-spacing:-.1px}
.item .q{color:var(--text);font-weight:700;font-size:11.8px;line-height:13.6px;text-align:justify;letter-spacing:-.15px}
.item .best{margin-top:13px;text-align:justify}
.item .best b{color:var(--blue);font-weight:600}
.item .note{margin-top:12px;text-align:justify}
.num{position:absolute;width:26px;height:26px;border-radius:50%;background:radial-gradient(circle at 40% 35%,#3e8fd6,var(--blue-dark));color:#fff;font-weight:700;font-size:12px;display:flex;align-items:center;justify-content:center;box-shadow:0 1px 2px rgba(0,0,0,.3)}
.url{position:absolute;left:61px;top:628px;font-size:19px;color:var(--text)}
.url b{color:var(--blue);font-weight:700}
.brand{position:absolute;left:884px;top:592px;display:flex;align-items:center;gap:12px}
.brand-dot{width:40px;height:40px;border-radius:50%;background:var(--blue)}
.brand-name{font-weight:600;font-size:22px;color:var(--blue);letter-spacing:1px}
.page-no{position:absolute;left:1116px;top:588px;width:50px;height:50px;border-radius:50%;background:radial-gradient(circle at 40% 35%,#3e8fd6,var(--blue-dark));color:#fff;font-weight:700;font-size:32px;display:flex;align-items:center;justify-content:center}
.foot-bar{position:absolute;left:0;top:663px;width:1200px;height:12px;display:flex}
.foot-bar .a{width:602px;background:var(--blue)}
.foot-bar .b{flex:1;background:var(--grey)}
</style>
</head>
<body>
<main class="slide">
  <div class="rule rule-left"></div>
  <div class="rule rule-right"></div>
  <h1 class="kicker">Non-Control Capital Questionnaire</h1>

  <svg class="banner" viewBox="0 0 1308 107" preserveAspectRatio="none" aria-hidden="true">
    <polygon points="0,0 170,0 133,107 0,107" fill="#38393b"/>
    <polygon points="180,0 1165,0 1128,107 143,107" fill="#1f6fb8"/>
    <polygon points="1176,0 1308,0 1308,107 1139,107" fill="#38393b"/>
  </svg>
  <h2 class="banner-title"><span>The Critical Questions to Ask of</span><span>Any Prospective Non-Control Investor</span></h2>

  <svg class="tab" viewBox="0 0 220 34" aria-hidden="true">
    <polygon points="8,0 22,0 14,34 0,34" fill="#1f6fb8"/>
    <polygon points="26,0 202,0 194,34 18,34" fill="#38393b"/>
    <polygon points="206,0 220,0 212,34 198,34" fill="#1f6fb8"/>
  </svg>
  <div class="tab-label">Questions</div>

  <div class="num" style="left:17px;top:251px">1</div>
  <section class="item" style="left:61px;top:253px">
    <p class="q">How many years has the firm been investing Non-Control Capital?</p>
    <p class="best"><b>Best Answer:</b> 5+ years investing as a team within the current firm</p>
    <p class="note">Indicates comfort and experience evaluating and making NCC investments with each other and increases likelihood of close</p>
  </section>

  <div class="num" style="left:17px;top:345px">2</div>
  <section class="item" style="left:61px;top:348px">
    <p class="q">&nbsp;How may fully-invested Non-Control Capital funds in the firm’s history?</p>
    <p class="best"><b>Best Answer:</b> 2+ fully-invested funds</p>
    <p class="note">Indicates experience and ability to close deals with the current regime—those firms without it may only be testing the waters and not have a long-term commitment to NCC investing</p>
  </section>

  <div class="num" style="left:17px;top:455px">3</div>
  <section class="item" style="left:61px;top:457px">
    <p class="q">What percentage of the firm’s voting investment committee are full-time Non-Control Capital investors?</p>
    <p class="best"><b>Best Answer:</b> Super-majority Indicates commitment, experience, and focus on NCC and overcomes dependency on buyout heritage, if any</p>
  </section>

  <div class="num" style="left:17px;top:537px">4</div>
  <section class="item" style="left:61px;top:539px">
    <p class="q">What is the number of Non-Control Capital investments made with the current firm and team?</p>
    <p class="best"><b>Best Answer:</b> 20+ Indicates long-term experience and comfort with current team, investment committee, and NCC investment assessment</p>
  </section>

  <div class="num" style="left:596px;top:266px">5</div>
  <section class="item" style="left:644px;top:267px">
    <p class="q">What percentage of portfolio investments made are “sponsorless” (those without a change-of-control investor)?</p>
    <p class="best"><b>Best Answer:</b> 80%+ of all investments closed in the last 5 years (assumes current transaction is also sponsorless)</p>
    <p class="note">Indicates ability to add-value as a sole minority investor and not simply as a back-up to another sponsor</p>
  </section>

  <div class="num" style="left:596px;top:386px">6</div>
  <section class="item" style="left:644px;top:389px">
    <p class="q">Can the investor show quantifiable proof of their ability to assist portfolio companies with growth and improvement (assumes more than 20 exited Non-Control investments)?</p>
    <p class="best"><b>Best Answer:</b> Yes (company owners should evaluate investors on actual historical revenue, EBITDA, and employee growth impact and the results should exceed what the current management has achieved on their own over the past 3 years)</p>
    <p class="note">Indicates true value-added ability to help owners grow their businesses. Those without proof of their impact, or who are unwilling to disclose it, should be excluded</p>
  </section>

  <p class="url">www.<b>pinebrookharbourfund</b>.com</p>

  <div class="brand">
    <span class="brand-dot"></span>
    <span class="brand-name">PINEBROOK</span>
  </div>

  <div class="page-no">2</div>

  <div class="foot-bar"><span class="a"></span><span class="b"></span></div>
</main>
</body>
</html>
```